Website Re-Design and Refresh

We are looking for a redesign of www.brightmeadow-example.com the deliverable is a graphic which will be used as a template for the main site.
The Logo will remain the same
The Video currently shown must be included in your submission
Search Element must be included, this should be better visible than it is currently
All navigation current on the left is to be moved to the right.
Top left column should be a “Quick Quotation” element. It should stand out and draw the eye as that is the conversion that we aim for on our site. This is the purpose of the site to attract these.
Add Testimonials navigation that users can click upon.
Below this element on the right “Recent Posts” should become Latest News”
We want users to see how much press coverage the site has had, the following UK’s news logos should be used Courier, Morning Ledger, NVR and The Wayfarer.
Please use the current text from our site but make some main features which we want to draw attention to. 5 points and use fake text, using a bullet point, icon, graphic or colour to make it stick out the most.
Large Guarantee, shown through a Seal graphic. An example of this type of style is attached.
Updates

Please note that as per the brief we want to havenews/contact forms down the left hand side of the page. This is to comply with “F”shapeeye pattern which shows that users look mostly on the left of webpages.

Please make the quick quotes more distinctive and use of thefields suggested in the brief.

As you appear to like using vivid colours, please see thefollowing examples we like of vivid colours.

 

http://media.tallcrane-example.com/cpw-sales/static/images/common/global_nav/nnp_03.png

http://media.tallcrane-example.com/cpw-sales/static/sections/homepage/2012_04/images/ban_big_promises.png

http://media.tallcrane-example.com/cpw-sales/static/images/landing_pages/mobile_phones/April_2012/mp_hero2_v3.jpg

http://media.tallcrane-example.com/cpw-sales/static/sections/upgrades/images/sidebanner_payg_upgrades.gif

Pleaseamend your designs so that they adhere to the following:

 

Thereis a quick quotation form, as per brief, next to the video positionedon the left, the video on the right so they are the first items the userssee. 

 

The"seal" guarantee should be top right and 

Newsand Testimonials should be on the right hand side

 

Inthe main content text area please use latin ipsom lorem text and put 5 bulletpoints in large writing and latin below. Such as:

 

Lorem Ipsum 

Lorem Ipsum 

Lorem Ipsum 

Lorem Ipsum 

Lorem Ipsum 

 

Lorem Ipsum is simply dummy text ofthe printing and typesetting industry. Lorem Ipsum has been the industry'sstandard dummy text ever since the 1500s, when an unknown printer took a galleyof type and scrambled it to make a type specimen book. It has survived not onlyfive centuries, but also the leap into electronic typesetting, remainingessentially unchanged. It was popularised in the 1960s with the release ofLetraset sheets containing Lorem Ipsum passages, and more recently with desktoppublishing software like Quorin SheetSmith including versions of Lorem Ipsum.

The following design is a good indication of style and the use of bright colors. Although the positioning of some elements is not as per the brief. 

Please see best deigns so far:

Target Market(s)

Business To Business

Industry/Entity Type

News

Requirements
Must have
• The Logo will remain the same
Top right should be a “Quick Quotation” element. It should stand out and draw the eye as that is the conversion that we aim for on our site. This is the purpose of the site to attract these.

```html
<!DOCTYPE html>
<html lang="en">
<head>
<meta charset="utf-8">
<title>Brightmeadow – Reputation Management</title>
<link rel="stylesheet" href="https://fonts.googleapis.com/css2?family=Roboto+Condensed:wght@400;700&family=Roboto:wght@400;500;700&display=swap">
<style>
:root{
  --page:#f1f1f1;
  --header-top:#ffffff;
  --header-bottom:#e2e2e2;
  --text:#3c3c3c;
  --green:#7cb032;
  --green-dark:#5f9a22;
  --green-light:#9ccc55;
  --magenta:#b5137f;
  --orange:#f26d1f;
  --navy:#0d3a78;
  --band:#dedede;
  --footer:#d8d8d8;
  --line:#cfcfcf;
  --press:#2a2a2a;
}
*{box-sizing:border-box;margin:0;padding:0}
html,body{width:1059px;height:1200px;overflow:hidden;background:var(--page);font-family:"Roboto",Arial,sans-serif;color:var(--text)}
.page{position:relative;width:1059px;height:1200px;overflow:hidden}
.abs{position:absolute}
.cond{font-family:"Roboto Condensed","Arial Narrow",sans-serif}

.site-header{left:0;top:0;width:1059px;height:139px;background:linear-gradient(var(--header-top),var(--header-bottom));box-shadow:0 2px 4px rgba(0,0,0,.12)}
.brand{left:104px;top:55px;font-size:34px;font-weight:700;color:var(--green-dark);display:flex;align-items:center;gap:10px}
.brand-dot{width:22px;height:22px;background:var(--green);border-radius:50%}
.call{left:709px;top:39px;font-size:20px;color:#555;letter-spacing:.5px}
.search{left:667px;top:79px;width:287px;height:27px;display:flex}
.search-input{flex:1;border:1px solid #c9c9c9;border-right:none;border-radius:4px 0 0 4px;background:#fff;font-size:12px;color:#999;padding:6px 13px}
.search-btn{width:74px;background:linear-gradient(var(--green-light),var(--green-dark));border-radius:0 4px 4px 0;color:#fff;font-size:17px;text-align:center;line-height:27px}

.main-nav{left:106px;top:138px;width:848px;height:35px;background:linear-gradient(#fff,#f3f3f3);border:1px solid var(--line);display:flex;align-items:center;justify-content:center;font-size:16px;color:#666}
.main-nav span{padding:0 14px;border-left:1px solid #ccc;line-height:16px}
.main-nav span:first-child{border:none}

.quote{left:103px;top:199px;width:324px;height:235px;background:linear-gradient(135deg,#a7d060,var(--green-dark));border:1px solid #8ab84a;border-radius:4px}
.quote h2{position:absolute;left:32px;top:8px;font-size:19px;color:#2f4a10}
.field{position:absolute;left:30px;width:269px;height:25px;background:linear-gradient(#fff,#eee);border-radius:8px;font-size:14px;color:#333;padding:4px 10px}
.submit{position:absolute;left:115px;top:198px;width:90px;height:28px;background:linear-gradient(#fafafa,#cfe3a6);border:1px solid #7a9e3c;border-radius:4px;font-size:13px;font-weight:700;color:#3d4f20;text-align:center;line-height:26px}

.why{left:447px;top:199px;width:507px;height:235px;background:#fff;border-radius:4px}
.why h2{position:absolute;left:37px;top:22px;font-size:21px;color:#3a3a3a}
.why ul{position:absolute;left:37px;top:60px;width:340px;list-style:none;font-family:"Roboto Condensed",sans-serif;font-size:10.5px;line-height:21.7px;color:#333}
.why li{padding-left:11px;position:relative}
.why li::before{content:"";position:absolute;left:0;top:9px;width:5px;height:5px;border-radius:50%;background:#333}
.more{position:absolute;right:26px;bottom:14px;font-size:10px;color:#555;display:flex;align-items:center;gap:5px}
.more i{width:15px;height:15px;border-radius:50%;background:#ddd;color:#fff;font-style:normal;font-size:9px;text-align:center;line-height:15px}

.feature{left:106px;top:454px;width:848px;height:262px;background:#fff;border-radius:4px}
.seal{position:absolute;left:28px;top:38px;width:106px;height:106px;border-radius:50%;background:radial-gradient(circle,#f7c548 45%,#d79a22 60%,#f3e3b0 75%,#c9c9c9 100%)}
.t-rep{position:absolute;left:133px;top:8px;font-size:45px;font-weight:700;color:var(--magenta);line-height:1.1}
.t-chg{position:absolute;left:199px;top:50px;font-size:45px;font-weight:700;color:var(--green-dark);line-height:1.1}
.t-60{position:absolute;left:136px;top:82px;font-size:68px;font-weight:700;color:var(--orange);line-height:1.1}
.t-days{position:absolute;left:210px;top:104px;font-size:30px;font-weight:700;color:var(--orange);line-height:1.1}
.t-money{position:absolute;left:57px;top:152px;font-size:26px;font-weight:700;color:var(--navy);line-height:1.1}
.note{position:absolute;left:45px;top:190px;width:280px;font-size:8.3px;line-height:13.8px;color:#222}
.video{position:absolute;left:391px;top:8px;width:447px;height:244px;background:#000}

.band{top:735px;height:35px;background:var(--band)}
.band h2{font-size:22px;color:#3c3c3c;padding:6px 18px}
.list{list-style:none;font-size:10.5px;line-height:17px;color:#444}
.list li{position:relative;padding-left:31px;margin-bottom:8px}
.list li::before{content:"";position:absolute;left:10px;top:5px;width:7px;height:7px;background:#999}
.news li{text-decoration:underline;margin-bottom:9px;line-height:15px}
.rule{left:105px;top:866px;width:323px;border-top:1px solid #555}

.press{display:flex;align-items:center;justify-content:center;text-align:center;background:#fff;color:var(--press);font-weight:700;font-size:17px}

.site-footer{left:0;top:1001px;width:1059px;height:199px;background:var(--footer)}
.foot-nav{position:absolute;left:0;top:18px;width:1059px;text-align:center;font-size:11px;color:#444}
.foot-nav span{padding:0 7px;border-left:1px solid #999}
.foot-nav span:first-child{border:none}
.foot-brand{position:absolute;left:160px;top:76px;font-size:26px;font-weight:700;color:var(--green-dark);display:flex;align-items:center;gap:8px}
.foot-brand .brand-dot{width:16px;height:16px}
.copy{position:absolute;left:160px;top:128px;font-size:11px;color:#444}
.vrule{position:absolute;top:55px;height:98px;border-left:1px solid #bbb}
.fseal{position:absolute;left:409px;top:67px;width:64px;height:64px;border-radius:50%;background:radial-gradient(circle,#f7c548 45%,#d79a22 60%,#f3e3b0 75%,#bbb 100%)}
.ftext{position:absolute;left:488px;top:58px;width:165px;font-size:10.7px;line-height:17px;color:#333}
.follow{position:absolute;left:693px;top:58px;font-size:14px;color:#333}
.soc{position:absolute;width:97px;height:18px;background:linear-gradient(#fff,#e6e6e6);border:1px solid #c4c4c4;font-size:7.5px;color:#333;display:flex;align-items:center;gap:8px}
.soc i{width:19px;height:18px}
</style>
</head>
<body>
<div class="page">

  <header class="site-header abs">
    <div class="brand abs"><span class="brand-dot"></span>Brightmeadow</div>
    <div class="call abs">Call:&nbsp; 0800 555 0132</div>
    <div class="search abs"><div class="search-input">Type your keyword hear...</div><div class="search-btn cond">Search</div></div>
  </header>

  <nav class="main-nav abs cond">
    <span><svg width="17" height="15" viewBox="0 0 17 15"><path d="M8.5 1 1 8h2v6h4V10h3v4h4V8h2z" fill="#8fc98f"/></svg></span>
    <span>Reputation Management</span>
    <span>Online Reputation Management - ORM</span>
    <span>Brand Protection</span>
    <span>Price</span>
  </nav>

  <section class="quote abs">
    <h2 class="cond">Quick Quotation</h2>
    <div class="field cond" style="top:35px">Name</div>
    <div class="field cond" style="top:66px">Email</div>
    <div class="field cond" style="top:98px">Contact No.</div>
    <div class="field cond" style="top:131px;height:57px">Query</div>
    <div class="submit cond">Submit</div>
  </section>

  <section class="why abs">
    <h2 class="cond">Why Brightmeadow?</h2>
    <ul>
      <li>Lorem ipsum dolor sit amet, consectetur adipiscing elit. Aenean sit amet odio in nulla lacinia malesuada. Eiam arcu</li>
      <li>Rutrum sit amet lacinia non, sodales nec est. Praesent purus massa,</li>
      <li>aliquet non bibendum nec, tempor sed elit. Suspendisse</li>
      <li>sodales pretium mauris, a lacinia massa blandit euismod.</li>
      <li>Fusce suscipit interdum risus id tristique. Suspendisse at nibh quis ante hendrerit luctus sit amet vitae leo.</li>
    </ul>
    <div class="more"><i>&gt;</i>Read More..</div>
  </section>

  <section class="feature abs">
    <div class="seal" role="img" aria-label="60 day satisfaction guarantee seal"></div>
    <div class="t-rep cond">Profile</div>
    <div class="t-chg cond">Renewal</div>
    <div class="t-60 cond">60</div>
    <div class="t-days cond">days</div>
    <div class="t-money cond">Money Back Guarantee*</div>
    <p class="note">&nbsp;&nbsp;&nbsp;* Lorem ipsum dolor sit amet, consectetur adipiscing elit. Aenean sit amet odio in nulla lacinia malesuada. Lorem ipsum dolor sit amet, consectetur adipiscing elit. Aenean sit amet odio in nulla lacinia malesuada.</p>
    <div class="video">
      <svg class="abs" style="left:225px;top:105px" width="32" height="36" viewBox="0 0 32 36"><path d="M0 0 32 18 0 36z" fill="#555"/></svg>
    </div>
  </section>

  <div class="band abs" style="left:106px;width:375px"><h2 class="cond">Testimonials</h2></div>
  <div class="band abs" style="left:481px;width:471px"><h2 class="cond" style="padding-left:17px">Media Coverage</h2></div>

  <ul class="list abs" style="left:106px;top:781px;width:300px">
    <li>Lorem ipsum dolor sit amet, consectetur adipiscing elit. Aenean sit amet odio in nulla lacinia.</li>
    <li>Lorem ipsum dolor sit amet, consectetur adipiscing Lorem ipsum dolor sit.</li>
  </ul>
  <div class="rule abs"></div>
  <h2 class="abs cond" style="left:121px;top:870px;font-size:22px;color:#3c3c3c">Latest News</h2>
  <ul class="list news abs" style="left:106px;top:903px;width:300px">
    <li>Lorem ipsum dolor sit amet, consectetur adipiscing elit. Aenean sit.</li>
    <li>Lorem ipsum dolor sit amet, consectetur adipiscing elit. Aenean sit amet odio in nulla lacinia malesuada.</li>
  </ul>

  <div class="press abs" style="left:494px;top:810px;width:79px;height:59px;font-size:13px;line-height:15px">NVR World News</div>
  <div class="press abs" style="left:589px;top:809px;width:193px;height:38px">Morning Ledger</div>
  <div class="press abs" style="left:793px;top:807px;width:156px;height:47px">The Wayfarer</div>
  <div class="press abs" style="left:494px;top:898px;width:169px;height:50px">NVR</div>
  <div class="press abs" style="left:685px;top:876px;width:266px;height:72px">The Sunday Courier</div>

  <footer class="site-footer abs">
    <div class="foot-nav"><span>Home</span><span>Reputation Management</span><span>Online Reputation Management - ORM</span><span>Brand Protection</span><span>Price</span><span>Contact us</span><span>Disclaimer</span><span>Privacy policy</span></div>
    <div class="foot-brand"><span class="brand-dot"></span>Brightmeadow</div>
    <div class="copy">Copyright 2012. All right reserved 2012.</div>
    <div class="vrule" style="left:387px"></div>
    <div class="fseal" role="img" aria-label="60 day satisfaction guarantee seal"></div>
    <p class="ftext">* Lorem ipsum dolor sit amet, consectetur adipiscing elit. Aenean sit amet odio in nulla lacinia malesuada. Lorem ipsum dolor sit amet, consectetur adipi-</p>
    <div class="vrule" style="left:668px"></div>
    <div class="follow">Follow us</div>
    <div class="soc" style="left:691px;top:85px"><i style="background:#f08a1c"></i>Subscribe RSS</div>
    <div class="soc" style="left:804px;top:85px"><i style="background:#5aaee0"></i>Follow my Chirps</div>
    <div class="soc" style="left:691px;top:114px"><i style="background:#3b5b98"></i>Find on Circlebook</div>
    <div class="soc" style="left:804px;top:114px"><i style="background:#c8392b"></i>Plusway Page</div>
  </footer>

</div>
</body>
</html>
```